Car transport business

We need a new business card design. Attached is our old card sample. I would just like to adjust the logo colors (blue and red) to be brighter. I changed my name to the brighter red and the word dispatcher to a brighter blue as an example. But you can adjust those colors further. And then perhaps you can use the same colors for the card design but use your imagination.

As a suggestion so the card stands out I would like to add a clip art of car carrier truck. Attached are examples of that as well

```html
<!DOCTYPE html>
<html lang="en">
<head>
<meta charset="utf-8">
<title>Summit Haul — Business Card</title>
<link rel="stylesheet" href="https://fonts.googleapis.com/css2?family=Roboto:wght@400;500;700;900&display=swap">
<style>
  :root{
    --bg:#2a2a2c;
    --ink-black:#0d0d0e;
    --paper:#ffffff;
    --brand-blue:#1f78d1;
    --brand-red:#e8232a;
    --text-grey:#555a60;
    --art-grey:#d9d9db;
  }
  *{margin:0;padding:0;box-sizing:border-box}
  html,body{width:1200px;height:900px;overflow:hidden}
  body{
    background:var(--bg);
    font-family:'Roboto',sans-serif;
    display:flex;flex-direction:column;align-items:center;justify-content:center;gap:22px;
  }
  .card{
    width:735px;height:420px;position:relative;overflow:hidden;
    box-shadow:0 10px 30px rgba(0,0,0,.45);
  }
  /* Back side */
  .card--back{background:var(--ink-black)}
  .card--back .brand{position:absolute;left:120px;top:140px}
  .card--back .back-web{
    position:absolute;left:0;right:0;top:300px;text-align:center;
    font-size:21px;font-weight:700;letter-spacing:.5px;color:var(--brand-blue);
  }
  .card--back .back-web span{color:var(--brand-red)}
  /* Brand block */
  .brand{display:flex;align-items:center;gap:14px}
  .brand__dot{width:22px;height:22px;border-radius:50%;background:var(--brand-red);flex:none}
  .brand__name{
    font-weight:900;font-size:58px;line-height:1;letter-spacing:2px;
    color:var(--brand-blue);text-transform:uppercase;
  }
  .brand__tag{
    display:block;margin-top:6px;font-size:16px;font-weight:400;letter-spacing:4px;
    color:var(--brand-blue);text-transform:uppercase;
  }
  /* Front side */
  .card--front{background:var(--paper)}
  .card--front .brand{position:absolute;left:60px;top:118px}
  .card--front .brand__name{font-size:44px}
  .card--front .brand__tag{font-size:12.5px;letter-spacing:3px}
  .truck-art{
    position:absolute;right:0;top:20px;width:370px;height:300px;
    background:linear-gradient(160deg,#eeeeef 0%,var(--art-grey) 100%);
  }
  .person{position:absolute;left:95px;top:228px}
  .person__name{font-size:30px;font-weight:900;color:var(--brand-red);letter-spacing:.5px;line-height:1}
  .person__role{font-size:19px;font-weight:500;color:var(--brand-blue);margin-top:3px}
  .contact{list-style:none;position:absolute;left:120px;top:298px;font-size:17px;color:var(--text-grey);line-height:23px}
  .contact li{display:flex;align-items:center;gap:10px}
  .contact svg{width:14px;height:14px;flex:none}
  .front-web{position:absolute;left:146px;top:372px;font-size:19px;font-weight:500;color:var(--brand-blue)}
  .base-band{position:absolute;left:0;right:0;bottom:0;height:10px;background:var(--brand-blue)}
</style>
</head>
<body>

<section class="card card--back" aria-label="Card back">
  <div class="brand">
    <span class="brand__dot"></span>
    <div>
      <span class="brand__name">Summit Haul</span>
      <span class="brand__tag">The auto transport professionals</span>
    </div>
  </div>
  <p class="back-web">www.Summit<span>Haul</span>co.com</p>
</section>

<section class="card card--front" aria-label="Card front">
  <div class="truck-art" role="img" aria-label="Black and white line illustration of a car carrier truck with an empty upper deck"></div>

  <div class="brand">
    <span class="brand__dot"></span>
    <div>
      <span class="brand__name">Summit Haul</span>
      <span class="brand__tag">The auto transport professionals</span>
    </div>
  </div>

  <div class="person">
    <p class="person__name">DAN MORROW</p>
    <p class="person__role">Dispatcher</p>
  </div>

  <ul class="contact">
    <li>
      <svg viewBox="0 0 16 16" aria-hidden="true"><path fill="var(--brand-blue)" d="M3.6 1.5l2.2 2.6-1.3 1.6c.9 2 2.5 3.6 4.5 4.6l1.6-1.3 2.6 2.2-1.4 2.3C7 13.3 2.7 9 1.3 3z"/></svg>
      555-210-0143
    </li>
    <li>
      <svg viewBox="0 0 16 16" aria-hidden="true"><rect x="4" y="1" width="8" height="14" rx="1.5" fill="none" stroke="var(--brand-blue)" stroke-width="1.6"/></svg>
      555-210-0178
    </li>
    <li>
      <svg viewBox="0 0 16 16" aria-hidden="true"><rect x="1" y="3" width="14" height="10" fill="var(--brand-blue)"/><path d="M1 3l7 6 7-6" fill="none" stroke="#fff" stroke-width="1.3"/></svg>
      summithaulco@mail.com
    </li>
  </ul>

  <p class="front-web">SummitHaulco.com</p>
  <div class="base-band"></div>
</section>

</body>
</html>
```